Website for the posting of RFQ from companies

BRIGHTOWL, a website for posting RFQ from government and companies.
Slogan: Promoting ethical and transparent business practices

Designed in HTML5 and responsive.
Government and companies can upload RFQ (request for quotation) advertisements through a back-end which can be searchable by companies interested in submitting quotes to the companies.

Companies once registered, get a username and logon to access back-end to load their advertisements for RFQ.

Users/ entrepreneurs also register and based on their subscription can access certain advertised RFQ information.

Also a platform where companies can notify other businesses of their commodities on hand. Example small mining company, small fishing company, farm growing fruits and veggies.

Weekly newsletter with latest uploaded RFQ information sent to users.
RFQ advert should display how often it was viewed. also display a button to contact company for more information.

Users register to receive sms and email notification when tenders of interest posted in their categories/ industry of interest.

Competitors:
Qu-biddesk.co.za
Rbidhouse.gov.za
Quickbidroom.co.za
Bidpilotx.co.za
Marketvine.net

Target Market(s)

Business people

Industry/Entity Type

Business

Coding

Coded - Design and coding required

Number of Pages Required

5+ page

Font styles to use
Sans Serif

Requirements
Must have
• simple clean design
• Html5
• Responsive
Nice to have
• Better and improved Design compared to my competitors
• Use of African models in pictures
Should not have
• dark background

```html
<!DOCTYPE html>
<html lang="en">
<head>
<meta charset="utf-8">
<title>Brightowl Trading</title>
<link rel="stylesheet" href="https://fonts.googleapis.com/css2?family=Raleway:wght@400;500;600&family=Open+Sans:wght@400;600&display=swap">
<style>
:root{
  --navy:#0b4f7e;
  --navy-deep:#0a3a5e;
  --sky:#3fb2f0;
  --sky-light:#5cc5f7;
  --accent:#2a9fe0;
  --heading:#1b4b78;
  --text:#7c8690;
  --text-dark:#4d5660;
  --line:#dfe3e7;
  --white:#ffffff;
}
*{margin:0;padding:0;box-sizing:border-box}
html,body{width:850px;height:1200px;overflow:hidden;background:var(--white)}
body{position:relative;font-family:"Open Sans",sans-serif;color:var(--text)}
.abs{position:absolute}
.header-band{left:0;top:0;width:850px;height:170px;background:linear-gradient(180deg,#0a5585 0%,var(--navy-deep) 100%)}
.account-links{right:135px;top:12px;font:600 7px "Open Sans",sans-serif;color:var(--white);letter-spacing:.2px}
.brand{left:135px;top:36px;font:500 18.5px "Raleway",sans-serif;color:var(--white)}
.lang-button{left:649px;top:42px;width:66px;height:19px;background:#1a7fc0;color:var(--white);font:400 8px "Open Sans",sans-serif;display:flex;align-items:center;justify-content:center;gap:4px}
.lang-button .swatch{width:11px;height:7px;background:#d8e4f0}
.main-nav{left:135px;top:78px;width:580px;height:35px;background:linear-gradient(180deg,var(--sky-light),#2fa5ea);display:flex;align-items:center;justify-content:space-around;padding:0 8px}
.main-nav a{font:500 11px "Raleway",sans-serif;color:var(--white);text-decoration:none}
.hero{left:135px;top:113px;width:580px;height:249px;background:linear-gradient(100deg,#d9ebf5 0%,#b9d9ec 45%,#8fb6cd 75%,#6f98b3 100%)}
.hero-title{left:166px;top:190px;font:400 21px "Raleway",sans-serif;color:var(--navy-deep)}
.hero-sub{left:166px;top:219px;font:500 12px "Raleway",sans-serif;color:var(--navy-deep)}
.hero-copy{left:166px;top:240px;width:215px;font:400 7px/10.5px "Open Sans",sans-serif;color:var(--navy-deep)}
.hero-dots{left:167px;top:270px;display:flex;gap:4px}
.hero-dots span{width:10px;height:10px;border-radius:50%;background:var(--white)}
.hero-dots span.active{background:#111}
.section-title{font:400 13.5px "Raleway",sans-serif;color:var(--heading)}
.copy{font:400 7px/11px "Open Sans",sans-serif;color:var(--text)}
.read-more{font:400 8.5px "Open Sans",sans-serif;color:var(--accent)}
.trend-box{top:575px;width:160px;height:120px;border:1px solid var(--line);padding:13px 0 0 14px}
.trend-box h3{font:400 10.5px "Raleway",sans-serif;color:var(--accent);margin-bottom:9px}
.bullets{list-style:none}
.bullets li{position:relative;padding-left:9px;font:400 6.5px/9px "Open Sans",sans-serif;color:var(--text-dark);margin-bottom:5.8px}
.bullets li::before{content:"";position:absolute;left:0;top:2px;border-left:3px solid var(--text-dark);border-top:2.5px solid transparent;border-bottom:2.5px solid transparent}
.tender-list li{margin-bottom:6px;font-size:6.6px}
.search-field{left:481px;top:406px;width:205px;height:23px;border:1px solid #cdd3d8;background:#fafbfc;font:400 7px "Open Sans",sans-serif;color:#6a737c;padding:7px 9px}
.search-field svg{position:absolute;right:7px;top:5px}
.tag-list{left:484px;top:440px;list-style:none}
.tag-list li{font:400 7.3px "Open Sans",sans-serif;color:var(--heading);height:18.4px}
.btn{display:flex;align-items:center;justify-content:center;font:500 10px "Raleway",sans-serif;color:var(--white);height:24px;top:576px}
.btn-download{left:483px;width:102px;background:linear-gradient(180deg,var(--sky-light),#2b9fe6)}
.btn-trial{left:592px;width:102px;background:linear-gradient(180deg,#125f94,var(--navy-deep))}
.cta-band{left:0;top:851px;width:850px;height:103px;background:linear-gradient(180deg,#4cbcf6,#2596ea)}
.cta-text{left:134px;top:881px;font:400 15px/22px "Raleway",sans-serif;color:var(--white)}
.cta-text span{font-size:13.5px}
.btn-join{left:599px;top:887px;width:94px;height:31px;border:2px solid var(--white);color:var(--white);font:500 11.5px "Raleway",sans-serif;display:flex;align-items:center;justify-content:center}
.news-title{left:135px;top:982px;font:400 14px "Raleway",sans-serif;color:var(--heading)}
.news-item{top:1010px;width:150px}
.news-item h4{font:400 7.8px "Open Sans",sans-serif;color:var(--text-dark);margin-bottom:3px}
.news-item p{font:400 6.5px/10.5px "Open Sans",sans-serif;color:var(--text)}
.news-banner{left:463px;top:998px;width:234px;height:60px;background:linear-gradient(90deg,#c9d8e2 0%,#e9f0f5 40%,#dfe8ef 75%,#c3d1db 100%)}
.banner-text{left:549px;top:1011px;color:var(--navy-deep)}
.banner-text b{display:block;font:600 11.5px "Raleway",sans-serif}
.banner-text i{display:block;font:500 8.5px "Raleway",sans-serif;font-style:normal}
.banner-text small{display:block;font:400 6.5px "Open Sans",sans-serif;margin-top:2px}
.footer{left:0;top:1114px;width:850px;height:86px;background:linear-gradient(180deg,#0b4c79,var(--navy-deep))}
.footer-nav{left:133px;top:1135px;font:500 10px "Raleway",sans-serif;color:var(--white)}
.copyright{left:133px;top:1158px;font:400 6px "Open Sans",sans-serif;color:#d6e3ee}
.social{left:655px;top:1136px;display:flex;gap:9px}
.social span{width:11px;height:11px;border-radius:50%;background:var(--white)}
</style>
</head>
<body>
<div class="abs header-band"></div>
<div class="abs account-links">SIGN UP &nbsp;|&nbsp; LOGIN</div>
<div class="abs brand">Brightowl Trading</div>
<div class="abs lang-button"><span class="swatch"></span>English &#9662;</div>
<nav class="abs main-nav">
  <a>Home</a><a>Search</a><a>Directory</a><a>About</a><a>Subscribe</a><a>Services</a><a>Support</a><a>Contact</a>
</nav>

<div class="abs hero" role="img" aria-label="Photo of a businesswoman in glasses drawing rising and falling chart lines on a glass screen"></div>
<div class="abs hero-title">NATOQUE PENATIBUS</div>
<div class="abs hero-sub">MAURIS LACUS VITAE FELIS</div>
<div class="abs hero-copy">In massa libero interdum nec interdum vel blandit sed nulla In ullamcorper est eget tempor cursus neque mi consec</div>
<div class="abs hero-dots"><span class="active"></span><span></span><span></span><span></span></div>

<h2 class="abs section-title" style="left:135px;top:383px">Entrepreneurs/tenderpreneurs</h2>
<p class="abs copy" style="left:135px;top:402px;width:320px">Curabitur iaculis tempus eros Curabitur vel mi sit amet magna malesuada ultrices Ut nisi erat fermentum vel congue id euismod in elit Fusce ultricies orci ac feugiat suscipit leo massa sodales velit et scelerisque mi tortor at ipsum cligula augue</p>
<a class="abs read-more" style="left:135px;top:440px">Read More</a>

<h2 class="abs section-title" style="left:135px;top:472px;line-height:18.5px">Governments, municipalities,<br>NGOs, private companies and individuals.</h2>
<p class="abs copy" style="left:135px;top:512px;width:320px">Curabitur iaculis tempus eros Curabitur vel mi sit amet magna malesuada ultrices Ut nisi erat fermentum vel congue id euismod in elit Fusce ultricies orci ac</p>
<a class="abs read-more" style="left:134px;top:538px">Read More</a>

<div class="abs trend-box" style="left:135px">
  <h3>Projects Currently Trending</h3>
  <ul class="bullets">
    <li>In massa libero interdum nec</li>
    <li>Anterdum vel blandit sed</li>
    <li>Nulla In ullamcorper est eget tempor</li>
    <li>Aursus neque mi consectetuer</li>
    <li>Mi a ultricies massa</li>
  </ul>
</div>
<div class="abs trend-box" style="left:301px">
  <h3>Tenders Currently Trending</h3>
  <ul class="bullets">
    <li>In massa libero interdum nec interdum vel blandit sed nulla In ullamco</li>
    <li>Rper est eget tempor cursus neque mi</li>
    <li>Consectetuer mi a ultricies massa</li>
    <li>Est sed nisl Class aptent taciti sociosqu</li>
  </ul>
</div>

<h2 class="abs section-title" style="left:135px;top:715px;font-size:12.5px">Recently Added Tenders</h2>
<ul class="abs bullets tender-list" style="left:137px;top:738px;width:320px">
  <li>Collection, dismantling, assessment, repair, overhaul, rewind, supply of spares, testing, painting, ...</li>
  <li>Supply and Installation of Irrigation Systems at Kwanele Vale College of Agriculture and Forestry</li>
  <li>Supply and Delivery of Hoses and Fittings</li>
  <li>NDFA: Refurbishment of ICT Disaster Recovery Plan (DRP), 27 Marula Road Workshop</li>
  <li>Renovation of Milking Parlor at Lwandile Agriculture and Rural Dev't Institute</li>
</ul>

<h2 class="abs section-title" style="left:479px;top:382px;color:var(--accent);font-size:12.5px">Quick Search Tags</h2>
<div class="abs search-field">Enter your Search here
  <svg width="12" height="12" viewBox="0 0 12 12"><circle cx="5" cy="5" r="4" fill="none" stroke="#b5bcc2" stroke-width="1.3"/><line x1="8" y1="8" x2="11" y2="11" stroke="#b5bcc2" stroke-width="1.3"/></svg>
</div>
<ul class="abs tag-list">
  <li>All available tenders,</li>
  <li>Tender loaded on that day,</li>
  <li>Tender reference number,</li>
  <li>Company or individual that issued the tender,</li>
  <li>Province/ region in which tendering services is required,</li>
  <li>Sector of issuer of the tender,</li>
  <li>Combination of issuer, region, sector and by country.</li>
</ul>
<div class="abs btn btn-download">Download Form</div>
<div class="abs btn btn-trial">Free Trail</div>

<div class="abs cover" style="left:483px;top:616px;width:67px;height:99px;background:linear-gradient(180deg,#1f3d2a,#173126)" role="img" aria-label="Book cover on a financial crisis"></div>
<div class="abs cover" style="left:557px;top:616px;width:66px;height:99px;background:linear-gradient(180deg,#1b5a5c,#12464a)" role="img" aria-label="Book cover on corporate finance law"></div>
<div class="abs cover" style="left:630px;top:616px;width:67px;height:99px;background:linear-gradient(180deg,#f2d43a,#c9b26a)" role="img" aria-label="Book cover of an investment guide"></div>
<div class="abs cover" style="left:483px;top:722px;width:67px;height:51px;background:linear-gradient(135deg,#ffffff,#8cc3e6)" role="img" aria-label="Press release distribution advert"></div>
<div class="abs cover" style="left:557px;top:722px;width:66px;height:51px;background:linear-gradient(135deg,#7ea34a,#c8b13a)" role="img" aria-label="Easy credit car finance advert"></div>
<div class="abs cover" style="left:630px;top:722px;width:67px;height:51px;background:linear-gradient(135deg,#bcc7cf,#e6d8d0)" role="img" aria-label="Book cover about economic reset"></div>
<div class="abs cover" style="left:483px;top:779px;width:67px;height:50px;background:linear-gradient(135deg,#a87a5a,#6a4a38)" role="img" aria-label="Close-up photo of a coin"></div>
<div class="abs cover" style="left:557px;top:779px;width:66px;height:50px;background:linear-gradient(135deg,#f3ead2,#d9c9a0)" role="img" aria-label="Credit building advert"></div>
<div class="abs cover" style="left:630px;top:779px;width:67px;height:50px;background:linear-gradient(135deg,#1a4fa8,#1c78d0)" role="img" aria-label="Blue stock market chart graphic"></div>

<div class="abs cta-band"></div>
<div class="abs cta-text">Curabitur iaculis tempus eros Curabitur vel mi sit amet magna<br><span>malesuada ultrices nisi erat fermentum vel congue euismod</span></div>
<div class="abs btn-join">JOIN US</div>

<h2 class="abs news-title">Latest News</h2>
<div class="abs news-item" style="left:135px">
  <h4>Nunc porta convallis pede</h4>
  <p>Etiam nulla massa pharetra facilisis volutpat n imperdiet sit amet sem Aliquam nec erat at purus cursus interdum Vestibulu</p>
</div>
<div class="abs news-item" style="left:296px">
  <h4>Donec quis mi sed magn</h4>
  <p>Etiam nulla massa pharetra facilisis volutpat imperdiet sit amet sem Aliquam nec erat at purus cursus interdum</p>
</div>
<div class="abs news-banner" role="img" aria-label="Photo of a businessman beside office towers for trading tips"></div>
<div class="abs banner-text"><b>BEST TRADING</b><i>FINANCE TIPS</i><small>Donec dictum lectus in odio</small></div>

<footer class="abs footer"></footer>
<div class="abs footer-nav">Home &nbsp;|&nbsp; Search &nbsp;|&nbsp; Directory &nbsp;|&nbsp; About &nbsp;|&nbsp; Subscribe &nbsp;|&nbsp; Services &nbsp;|&nbsp; Support &nbsp;|&nbsp; Contact</div>
<div class="abs copyright">© 2015 Company Name &nbsp;All right reserved &nbsp;Term of Use</div>
<div class="abs social" aria-label="Social links"><span></span><span></span><span></span></div>
</body>
</html>
```